Print materials for 3-star hotel

We are changing up our print materials (notepads, letterheads, key card jackets, small flyer for the room rates) We are a 3 star business hotel in the Philippines and have mainly used grey tones and clean, simple lines. See attached photos for logo and hotel interior photos.

Target Market(s)

Business

Contact Information for Business Card

Corvale Terrace Hotel
Lindwell Banca Avenue corner Tolenta St Cebu City 6000 Philippines
Tel: +63 32 481 7302
Mobile: +63 917 648 2095
www.corvaleterracehotel.example

Font styles to use
Serif
Sans Serif

Requirements
Must have
• Simple
• Readable font and font size
Nice to have
• Neutral colors, grey and taupes
Should not have
• No purples and bright blues

```html
<!DOCTYPE html>
<html lang="en">
<head>
<meta charset="utf-8">
<title>Corvale Terrace Hotel – Business Card</title>
<link rel="stylesheet" href="https://fonts.googleapis.com/css2?family=Cormorant+Garamond:wght@500&family=Open+Sans:wght@400;700&display=swap">
<style>
  :root {
    --backdrop: #3a332e;
    --card: #121212;
    --card-edge: #1d1d1d;
    --ink: #f2f2f2;
    --ink-soft: #b9b9b9;
    --ink-muted: #8a8a8a;
    --rule: #9a9a9a;
  }
  * { margin: 0; padding: 0; box-sizing: border-box; }
  html, body { width: 1200px; height: 864px; overflow: hidden; }
  body {
    background: var(--backdrop);
    display: flex;
    align-items: center;
    justify-content: center;
    gap: 40px;
    font-family: "Open Sans", Arial, sans-serif;
    color: var(--ink);
  }
  .card {
    width: 560px;
    height: 320px;
    background: linear-gradient(160deg, var(--card-edge), var(--card) 60%);
    border-radius: 4px;
    box-shadow: 0 14px 30px rgba(0,0,0,.45);
    position: relative;
  }
  /* front */
  .card-front {
    display: flex;
    flex-direction: column;
    align-items: center;
    justify-content: center;
  }
  .front-name {
    font-family: "Cormorant Garamond", Georgia, serif;
    font-weight: 500;
    font-size: 30px;
    letter-spacing: 5px;
    text-transform: uppercase;
    color: var(--ink-soft);
    display: flex;
    align-items: center;
    gap: 14px;
  }
  .front-mark {
    width: 14px; height: 14px;
    background: var(--ink-soft);
  }
  .front-web {
    margin-top: 42px;
    font-size: 12px;
    letter-spacing: 3px;
    color: var(--ink-muted);
  }
  /* back */
  .card-back {
    display: flex;
    align-items: center;
  }
  .back-brand {
    width: 270px;
    text-align: center;
    font-family: "Cormorant Garamond", Georgia, serif;
    font-weight: 500;
    font-size: 19px;
    letter-spacing: 4px;
    line-height: 1.5;
    text-transform: uppercase;
    color: var(--ink);
  }
  .back-rule {
    width: 1px;
    height: 200px;
    background: linear-gradient(transparent, var(--rule) 15%, var(--rule) 85%, transparent);
  }
  .back-details {
    padding-left: 22px;
    font-size: 12px;
    line-height: 1.45;
  }
  .person-name { font-weight: 700; font-size: 17px; letter-spacing: .5px; }
  .person-role { font-size: 12px; text-transform: uppercase; margin-bottom: 6px; }
  .address { margin-bottom: 4px; }
  .contact-list { list-style: none; }
  .contact-list li { display: flex; align-items: center; gap: 8px; }
  .contact-list svg { width: 11px; height: 11px; fill: var(--ink); flex: none; }
</style>
</head>
<body>
  <section class="card card-front">
    <div class="front-name"><span class="front-mark"></span>Corvale Terrace</div>
    <div class="front-web">www.corvaleterracehotel.example</div>
  </section>

  <section class="card card-back">
    <div class="back-brand">Corvale Terrace<br>Hotel</div>
    <div class="back-rule"></div>
    <div class="back-details">
      <div class="person-name">ELENA VARGO</div>
      <div class="person-role">President</div>
      <div class="address">Lindwell Banca Avenue corner Tolenta St<br>Cebu City 6000 Philippines</div>
      <ul class="contact-list">
        <li><svg viewBox="0 0 12 12"><path d="M1 3c0-1 1-2 2-2h6c1 0 2 1 2 2v1H8V3H4v1H1zM2 5h8l1 6H1z"/></svg>+63 32 481 7302</li>
        <li><svg viewBox="0 0 12 12"><path d="M3 0h6v12H3zM4 1v8h4V1z"/></svg>+63 917 648 2095</li>
        <li><svg viewBox="0 0 12 12"><path d="M3 0h6v4H3zM0 4h12v8H0zM2 6v2h8V6z"/></svg>+63 32 481 7309</li>
        <li><svg viewBox="0 0 12 12"><path d="M0 2h12v1L6 7 0 3zM0 4.5l6 4 6-4V10H0z"/></svg>elena@corvaleterracehotel.example</li>
        <li><svg viewBox="0 0 12 12"><path d="M6 0a6 6 0 1 0 0 12A6 6 0 0 0 6 0zm0 2a4 4 0 1 1 0 8 4 4 0 0 1 0-8z"/></svg>www.corvaleterracehotel.example</li>
      </ul>
    </div>
  </section>
</body>
</html>
```